Plate of the Raven: Half-Page Magazine Ad

advertisement in a travel magazine for a casual/fine dining restaurant in the heart of Whitehorse, Yukon
Needs to say that it is located in the Stonefield Hotel, 247 Larch Avenue.

Northern inspired cuisine
plateoftheraven.example

Don't need to use all the pictures

Dimensions: ad is a half-page, dimensions are 7.25" x 4.8".

Target Market(s)

Upscale dining, corporate travellers

Industry/Entity Type

Restaurant

Colors
0054AA
0677BA
7BADD7
CADEEF
E8F1F8
0094D4
00A9DD
6FCCEA
C7EBF8
E9F6FB
00AB8E
00BBA5
67D7C9
C6EFE9
E9F9F6

Requirements
Must have
• Restaurant logo
Nice to have
• Simple, clean design with upscale feel

```html
<!DOCTYPE html>
<html lang="en">
<head>
<meta charset="utf-8">
<title>Plate of the Raven – Half-Page Ad</title>
<link href="https://fonts.googleapis.com/css2?family=Bodoni+Moda:opsz,wght@6..96,400&family=Arimo:wght@400&display=swap" rel="stylesheet">
<style>
  :root {
    --navy: #0054aa;
    --blue: #0677ba;
    --blue-soft: #7badd7;
    --blue-pale: #cadeef;
    --blue-mist: #e8f1f8;
    --sky: #00a9dd;
    --sky-pale: #c7ebf8;
    --teal: #00ab8e;
    --teal-soft: #67d7c9;
    --teal-mist: #e9f9f6;
    --ink: #0d2440;
    --wood: #7a5a3e;
    --bar-grey: #8d8a84;
    --petal: #6b4fa0;
    --plate-meat: #7d4a3c;
    --plate-green: #a8b55a;
  }
  * { box-sizing: border-box; margin: 0; padding: 0; }
  html, body {
    width: 1200px; height: 789px; overflow: hidden;
    background: var(--blue-mist);
  }
  .ad {
    position: absolute; left: 0; top: 0;
    width: 1200px; height: 789px;
    background: var(--blue-mist);
    overflow: hidden;
  }
  .hero-interior {
    position: absolute; left: 0; top: 0; width: 1200px; height: 340px;
    background: linear-gradient(160deg, #cfc8bd 0%, var(--bar-grey) 35%, var(--wood) 75%, #5d4430 100%);
  }
  .info-panel {
    position: absolute; left: 0; top: 270px; width: 1200px; height: 519px;
    background: var(--blue-mist);
    border-top-left-radius: 240px 190px;
  }
  .headline {
    position: absolute; left: 70px; top: 395px;
    font-family: 'Bodoni Moda', serif; font-weight: 400;
    color: var(--ink); line-height: .92;
  }
  .headline__main {
    display: block; font-size: 96px; letter-spacing: -1px;
    transform: scaleX(.72); transform-origin: left;
  }
  .headline__sub {
    display: block; font-size: 44px; margin-top: 10px;
    color: var(--navy);
    transform: scaleX(.82); transform-origin: left;
  }
  .patio-photo {
    position: absolute; left: 860px; top: 240px; width: 290px; height: 320px;
    border-radius: 44px 44px 60px 44px;
    background: linear-gradient(170deg, var(--blue-soft) 0%, #a7a5a0 40%, #6c6a66 70%, var(--petal) 100%);
    box-shadow: 7px 8px 0 var(--blue-soft);
  }
  .cuisine-badge { position: absolute; left: 440px; top: 360px; width: 330px; height: 330px; }
  .cuisine-badge text {
    font-family: 'Bodoni Moda', serif; font-size: 27px; fill: var(--ink);
  }
  .sketch {
    position: absolute; left: 770px; top: 590px; width: 130px; height: 120px;
    background: radial-gradient(ellipse at 60% 45%, #bdbdbd 0%, #d8dde2 55%, var(--blue-mist) 80%);
  }
  .brand-name {
    position: absolute; left: 915px; top: 588px; width: 250px;
    font-family: 'Bodoni Moda', serif; font-weight: 400;
    font-size: 40px; line-height: .95; color: var(--navy);
  }
  .contact {
    position: absolute; left: 770px; top: 722px; width: 400px;
    font-family: 'Arimo', sans-serif; font-size: 16px; line-height: 1.45;
    color: var(--ink); text-align: center;
  }
</style>
</head>
<body>
  <article class="ad">
    <div class="hero-interior" role="img" aria-label="Restaurant interior with a bar counter, stools and wood floor"></div>
    <div class="info-panel"></div>

    <h1 class="headline">
      <span class="headline__main">OPEN</span>
      <span class="headline__main">EVENINGS</span>
      <span class="headline__sub">With A Summer Patio.</span>
    </h1>

    <svg class="cuisine-badge" viewBox="0 0 330 330" aria-label="Northern Inspired Cuisine">
      <defs>
        <path id="cuisine-arc" d="M35 215 A 130 130 0 0 1 295 215"/>
        <radialGradient id="plate-tones" cx="50%" cy="45%" r="60%">
          <stop offset="0%" stop-color="var(--plate-meat)"/>
          <stop offset="55%" stop-color="var(--plate-green)"/>
          <stop offset="100%" stop-color="#e8e4dc"/>
        </radialGradient>
      </defs>
      <text><textPath href="#cuisine-arc" startOffset="50%" text-anchor="middle">Northern Inspired Cuisine</textPath></text>
      <circle cx="169" cy="219" r="100" fill="var(--blue-soft)"/>
      <circle cx="165" cy="215" r="98" fill="url(#plate-tones)" role="img" aria-label="Plated dish of seared meat with greens"/>
    </svg>

    <div class="patio-photo" role="img" aria-label="Hotel exterior with patio seating and purple flower planters"></div>

    <div class="sketch" role="img" aria-label="Pencil sketch of an animal head"></div>
    <div class="brand-name">Plate<br>of the<br>Raven</div>

    <p class="contact">www.plateoftheraven.example<br>Stonefield Hotel, 247 Larch Avenue.</p>
  </article>
</body>
</html>
```